Corporate Business Card

Very professional, Modern, Not to busy, include phone address email, website
(253) 617-4930, 18761 52nd Avenue S, Kent, WA 98047, martin@plumlinegroup.com, varkoworks.com

Target Market(s)

Manufacturing

Industry/Entity Type

Aero, machining, manufacturing, Off road racing

Contact Information for Business Card

Phone, address email, website

```html
<!DOCTYPE html>
<html lang="en">
<head>
<meta charset="utf-8">
<title>Varko Works — Business Card</title>
<link rel="stylesheet" href="https://fonts.googleapis.com/css2?family=Montserrat:wght@700&family=Questrial&display=swap">
<style>
  :root {
    --navy: #17346c;
    --red: #d2232a;
    --paper: #ffffff;
  }
  * { margin: 0; padding: 0; box-sizing: border-box; }
  html, body { width: 1200px; height: 686px; overflow: hidden; background: var(--paper); }
  .card {
    position: relative;
    width: 1200px;
    height: 686px;
    background: var(--paper);
    overflow: hidden;
  }
  .card-frame { position: absolute; inset: 0; }
  .brand-name {
    position: absolute;
    left: 0; right: 0;
    top: 156px;
    text-align: center;
    font-family: "Montserrat", sans-serif;
    font-weight: 700;
    font-size: 54px;
    letter-spacing: 1px;
    color: var(--navy);
    line-height: 1;
  }
  .contact-list {
    position: absolute;
    left: 330px;
    width: 539px;
    top: 470px;
    list-style: none;
    text-align: center;
    font-family: "Questrial", sans-serif;
    font-size: 28px;
    color: var(--navy);
    line-height: 42.5px;
    letter-spacing: 0.2px;
  }
</style>
</head>
<body>
<main class="card">
  <svg class="card-frame" width="1200" height="686" viewBox="0 0 1200 686" aria-hidden="true">
    <!-- side bands -->
    <polygon class="side-band side-band--left" points="0,0 62,0 62,314 0,409" fill="var(--navy)"/>
    <polygon class="side-band side-band--right" points="1138,0 1200,0 1200,409 1138,314" fill="var(--navy)"/>

    <!-- contact panel outline -->
    <path class="contact-outline" d="M443,400 H376 A46,46 0 0 0 330,446 V686" fill="none" stroke="var(--navy)" stroke-width="2.2"/>
    <path class="contact-outline" d="M758,400 H823 A46,46 0 0 1 869,446 V686" fill="none" stroke="var(--navy)" stroke-width="2.2"/>

    <!-- icon connector -->
    <line x1="477" y1="398" x2="721" y2="398" stroke="var(--red)" stroke-width="2.2"/>

    <!-- phone icon -->
    <g class="icon icon--phone" transform="translate(477 398)">
      <circle r="25" fill="var(--red)"/>
      <path d="M-10,-10 l5,-2 l4,7 l-3,3 q3,6 9,9 l3,-3 l7,4 l-2,5 q-2,3 -6,2 q-14,-5 -19,-19 q-1,-4 2,-6z" fill="var(--paper)"/>
      <path d="M3,-10 a8,8 0 0 1 7,7 M3,-15 a13,13 0 0 1 12,12" fill="none" stroke="var(--paper)" stroke-width="1.8" stroke-linecap="round"/>
    </g>

    <!-- mail icon -->
    <g class="icon icon--mail" transform="translate(558 398)">
      <circle r="25" fill="var(--red)"/>
      <rect x="-13" y="-9" width="26" height="18" rx="1.5" fill="none" stroke="var(--paper)" stroke-width="2.2"/>
      <path d="M-13,-8 L0,3 L13,-8 M-13,9 L-4,-1 M13,9 L4,-1" fill="none" stroke="var(--paper)" stroke-width="2" stroke-linejoin="round"/>
    </g>

    <!-- location icon -->
    <g class="icon icon--pin" transform="translate(639 398)">
      <circle r="25" fill="var(--red)"/>
      <path d="M0,9 C-5,2 -9,-3 -9,-7 a9,9 0 0 1 18,0 C9,-3 5,2 0,9z" fill="var(--paper)"/>
      <circle cx="0" cy="-7" r="3.5" fill="var(--red)"/>
      <ellipse cx="0" cy="11" rx="10" ry="3.2" fill="none" stroke="var(--paper)" stroke-width="1.8"/>
    </g>

    <!-- globe icon -->
    <g class="icon icon--globe" transform="translate(721 398)" fill="none" stroke="var(--paper)" stroke-width="1.8">
      <circle r="25" fill="var(--red)" stroke="none"/>
      <circle r="12"/>
      <ellipse rx="5.5" ry="12"/>
      <line x1="0" y1="-12" x2="0" y2="12"/>
      <line x1="-12" y1="0" x2="12" y2="0"/>
      <path d="M-10,-6 H10 M-10,6 H10"/>
    </g>
  </svg>

  <h1 class="brand-name">Varko Works</h1>

  <ul class="contact-list">
    <li class="contact-phone">(253) 617-4930, 18761</li>
    <li class="contact-web">varkoworks.com</li>
    <li class="contact-address">52nd Avenue S, Kent, WA 98047</li>
    <li class="contact-email">martin@plumlinegroup.com</li>
  </ul>
</main>
</body>
</html>
```